Hair salon Business Card

Beauty Salon
I would like to see designs using sky blue and a soft orange. Mainly I would like my name ( Gloss N' Wave Salon ) used as the design

Industry/Entity Type

Business

Contact Information for Business Card

Gloss N'Wave Salon
318 E Maple Hyw #14
Linden Park, Ca 91840
909 555-2716

```html
<!DOCTYPE html>
<html lang="en">
<head>
<meta charset="utf-8">
<title>Gloss N'Wave Salon – Business Card</title>
<link rel="stylesheet" href="https://fonts.googleapis.com/css2?family=Lato:wght@400&display=swap">
<style>
  :root {
    --page-bg: #ecebe8;
    --card-bg: #ffffff;
    --soft-orange: #d17d0a;
    --sky-blue: #1b55b8;
    --ink: #1d1d1d;
    --on-orange: #ffffff;
  }
  * { margin: 0; padding: 0; box-sizing: border-box; }
  html, body {
    width: 1200px;
    height: 900px;
    overflow: hidden;
    background: var(--page-bg);
  }
  .canvas {
    position: relative;
    width: 1200px;
    height: 900px;
  }
  .card {
    position: absolute;
    background: var(--card-bg);
    border-radius: 14px;
    overflow: hidden;
    box-shadow: 0 6px 18px rgba(0,0,0,0.12);
  }
  .brand-name {
    position: absolute;
    font-family: "Lato", sans-serif;
    font-weight: 400;
    font-size: 32px;
    line-height: 1;
    white-space: nowrap;
    text-align: center;
  }
  .brand-mark {
    position: absolute;
    border-radius: 50%;
    background: var(--soft-orange);
  }

  /* Back side: contact details */
  .card-back {
    left: 78px; top: 35px;
    width: 588px; height: 362px;
  }
  .header-band {
    position: absolute;
    top: 40px;
    height: 104px;
    background: var(--soft-orange);
  }
  .header-band.left { left: 0; width: 387px; }
  .header-band.right { left: 491px; width: 97px; }
  .card-back .brand-name {
    left: 40px; top: 76px;
    width: 340px;
    color: var(--on-orange);
  }
  .card-back .brand-mark {
    left: 413px; top: 62px;
    width: 60px; height: 60px;
  }
  .contact {
    position: absolute;
    left: 0; width: 100%;
    text-align: center;
    font-family: "Lato", sans-serif;
    font-size: 15px;
    line-height: 1.2;
    color: var(--ink);
  }
  .contact.phone { top: 246px; }
  .contact.address { top: 286px; }
  .phone-icon {
    display: inline-block;
    width: 12px; height: 12px;
    vertical-align: -1px;
    margin-right: 6px;
  }

  /* Front side: name */
  .card-front {
    left: 390px; top: 505px;
    width: 564px; height: 351px;
  }
  .side-stripe {
    position: absolute;
    left: 12px; top: 0;
    width: 43px; height: 100%;
    background: var(--soft-orange);
  }
  .card-front .brand-name {
    left: 80px; top: 160px;
    width: 296px;
    text-align: right;
    color: var(--sky-blue);
  }
  .card-front .brand-mark {
    left: 392px; top: 148px;
    width: 56px; height: 56px;
  }
</style>
</head>
<body>
<main class="canvas">

  <section class="card card-back" aria-label="Business card back">
    <div class="header-band left"></div>
    <div class="header-band right"></div>
    <div class="brand-name">Gloss N'Wave Salon</div>
    <div class="brand-mark" aria-hidden="true"></div>

    <p class="contact phone">
      <svg class="phone-icon" viewBox="0 0 24 24" aria-hidden="true">
        <path fill="#d17d0a" d="M6.6 10.8a15.1 15.1 0 0 0 6.6 6.6l2.2-2.2a1 1 0 0 1 1-.25 11.4 11.4 0 0 0 3.6.57 1 1 0 0 1 1 1V20a1 1 0 0 1-1 1A17 17 0 0 1 3 4a1 1 0 0 1 1-1h3.5a1 1 0 0 1 1 1c0 1.25.2 2.45.57 3.57a1 1 0 0 1-.25 1z"/>
      </svg>909 555-2716
    </p>
    <p class="contact address">318 E Maple Hyw #14 Linden Park, Ca 91840</p>
  </section>

  <section class="card card-front" aria-label="Business card front">
    <div class="side-stripe"></div>
    <div class="brand-name">Gloss N'Wave Salon</div>
    <div class="brand-mark" aria-hidden="true"></div>
  </section>

</main>
</body>
</html>
```